Indy Film Production Company/Studio

We need a business card designed from an existing logo. We are a digital studio/production company that caters to creating genre entertainment, like Action, Horror, and martial arts. The card along with the logo will be used to Brand the company from letter heads to banners. The design will also be used for postcards and Brochures. It should be professional and masculine.
Updates

Thank you to all the designers who have participated. I'm narrowing down who it will be. Thank you again.

Target Market(s)

Investors, Networks, Producers, and actors

Industry/Entity Type

Film Production

Contact Information for Business Card

Teodoro Valbuena
Producer/Writer/Director
www.kestrelpicturehouse.example

Requirements
Must have
• Website address, Facebook icon and Twitter icon possibly in the back of the card.
Nice to have
• Logline of Company: Follow The Action.

```html
<!DOCTYPE html>
<html lang="en">
<head>
<meta charset="utf-8">
<title>Kestrel Picture House — Business Card</title>
<link href="https://fonts.googleapis.com/css2?family=Montserrat:wght@400;500;800&display=swap" rel="stylesheet">
<style>
  :root {
    --backdrop: #2b2b2b;
    --card-black: #050505;
    --stripe-white: #ffffff;
    --brand-red: #e8222b;
    --text-white: #f2f2f2;
  }
  * { margin: 0; padding: 0; box-sizing: border-box; }
  html, body {
    width: 1200px; height: 900px; overflow: hidden;
    background: var(--backdrop);
    font-family: "Montserrat", Arial, sans-serif;
  }
  .canvas {
    width: 1200px; height: 900px;
    display: flex; flex-direction: column;
    align-items: center; justify-content: center; gap: 40px;
  }
  .card {
    position: relative;
    width: 700px; height: 400px;
    background: var(--card-black);
    overflow: hidden;
  }
  .stripe {
    position: absolute; top: 0; bottom: 0;
    width: 34px; background: var(--stripe-white);
  }
  .stripe--left { left: 150px; }
  .stripe--right { left: 612px; }

  .brand {
    color: var(--brand-red);
    font-weight: 800;
    text-transform: uppercase;
    line-height: 0.95;
  }
  .brand__line { display: block; }

  /* Front */
  .card--front .front-content {
    position: absolute; left: 200px; right: 100px; top: 0; bottom: 0;
    display: flex; flex-direction: column; justify-content: center; align-items: center;
  }
  .card--front .brand { text-align: center; font-size: 54px; letter-spacing: 1px; }
  .card--front .brand__line--small { font-size: 27px; letter-spacing: 2px; margin-top: 6px; }
  .website {
    margin-top: 14px;
    color: var(--text-white);
    font-size: 17px; font-weight: 400; letter-spacing: 0.5px;
  }
  .logline {
    margin-top: 10px;
    color: var(--brand-red);
    font-size: 13px; font-weight: 500; letter-spacing: 3px;
    text-transform: uppercase;
  }

  /* Back */
  .card--back .back-content {
    position: absolute; left: 220px; right: 110px; top: 44px;
    display: flex; flex-direction: column; align-items: flex-end;
  }
  .card--back .brand { text-align: right; font-size: 40px; }
  .card--back .brand__line--small { font-size: 20px; letter-spacing: 1.5px; margin-top: 5px; }
  .person { margin-top: 16px; text-align: right; }
  .person__name {
    color: var(--brand-red); font-size: 24px; font-weight: 500;
    letter-spacing: 1.5px; text-transform: uppercase;
  }
  .person__title {
    color: var(--text-white); font-size: 13px; font-weight: 400;
    letter-spacing: 1.5px; text-transform: uppercase; margin-top: 2px;
  }
  .contacts {
    list-style: none; margin-top: 20px; align-self: flex-start;
    color: var(--text-white); font-size: 15px; line-height: 1.45;
  }
  .contacts__label { color: var(--brand-red); display: inline-block; width: 26px; font-weight: 500; }
  .social {
    list-style: none; margin-top: 12px; align-self: flex-start;
    display: flex; gap: 18px;
    color: var(--text-white); font-size: 13px;
  }
  .social__item { display: flex; align-items: center; gap: 8px; }
  .social__dot {
    width: 18px; height: 18px; border-radius: 50%;
    background: var(--brand-red); flex: none;
  }
</style>
</head>
<body>
<main class="canvas">
  <section class="card card--front" aria-label="Card front">
    <div class="stripe stripe--left"></div>
    <div class="stripe stripe--right"></div>
    <div class="front-content">
      <div class="brand">
        <span class="brand__line">Kestrel</span>
        <span class="brand__line brand__line--small">Picture House</span>
      </div>
      <p class="website">www.kestrelpicturehouse.example</p>
      <p class="logline">Follow The Action.</p>
    </div>
  </section>

  <section class="card card--back" aria-label="Card back">
    <div class="stripe stripe--left"></div>
    <div class="stripe stripe--right"></div>
    <div class="back-content">
      <div class="brand">
        <span class="brand__line">Kestrel</span>
        <span class="brand__line brand__line--small">Picture House</span>
      </div>
      <div class="person">
        <p class="person__name">Teodoro Valbuena</p>
        <p class="person__title">Producer/Writer/Director</p>
      </div>
      <ul class="contacts">
        <li><span class="contacts__label">P:</span>+330 2460-7731</li>
        <li><span class="contacts__label">E:</span>info@kestrelpicturehouse.example</li>
        <li><span class="contacts__label">W:</span>www.kestrelpicturehouse.example</li>
      </ul>
      <ul class="social" aria-label="Social profiles">
        <li class="social__item"><span class="social__dot"></span>/kestrelpicturehouse</li>
        <li class="social__item"><span class="social__dot"></span>@kestrelpictures</li>
      </ul>
    </div>
  </section>
</main>
</body>
</html>
```